Logo and Card design for KRV Home Solutions LLC

I need an edgier logo and business card designs. Current logo attached. I like the colors below. I would like the logo to incorporate a home in the design.
Title = Principal-Acquisitions
Email:KRVHOMESOLUTIONS@fernmail.example
555-214-0937
facebook
IG
2 sided business card with the front being contact info a slogan about selling a home fast. The back incorporating What we do. Buy houses, land, or commercial property as is. We find solutions to make the process of selling simple and fair.

Target Market(s)

Motivated house sellers.

Industry/Entity Type

Business

Contact Information for Business Card

Who we are: We are a Faith based Real Estate Investment Company. We pay cash for homes in any condition and can close quick. Whatever the reason you need to sell fast, we can help. We believe in creating win-win solutions to help you in your time of need. We care! We can help!

Logo Text

KRV Home Solutions LLC

Font styles to use
Sans Serif

Colors
33a6d7
0355a3
85abd2
cee9f5
9d9d9d
b2b2b2
ffffff

Requirements
Must have
• Old logo attached. I want something edgier.
• Company name, phone number, description on the back of what we can do. Pay all cash. Buy in as is condition. No fees,Commisions or closing costs.Close quick. No hassles with solutions to meet your unique situation.
• Call today for an offer within 24 hours.

```html
<!DOCTYPE html>
<html lang="en">
<head>
<meta charset="utf-8">
<title>KRV Home Solutions – Business Card</title>
<link href="https://fonts.googleapis.com/css2?family=Roboto:wght@400;500;700&family=Roboto+Condensed:wght@400;700&display=swap" rel="stylesheet">
<style>
  :root {
    --stage: #2b2b2d;
    --card-light: #ffffff;
    --card-dark: #1c2024;
    --brand-blue: #1f3f8f;
    --brand-navy: #0355a3;
    --text-grey: #4a4a4a;
    --name-grey: #5a5a5a;
    --text-white: #ffffff;
    --rule: #9d9d9d;
    --icon-blue: #85abd2;
  }
  * { box-sizing: border-box; margin: 0; padding: 0; }
  html, body { width: 1200px; height: 900px; overflow: hidden; }
  body {
    background: var(--stage);
    font-family: "Roboto", Arial, sans-serif;
    position: relative;
  }
  .card {
    position: absolute;
    left: 280px;
    width: 640px;
    height: 366px;
    overflow: hidden;
  }
  /* Back side */
  .card--about {
    top: 60px;
    background: var(--card-light);
    text-align: center;
    color: var(--text-grey);
    padding: 44px 36px 0;
  }
  .brand {
    display: inline-flex;
    align-items: center;
    gap: 12px;
    margin-bottom: 30px;
  }
  .brand__mark {
    width: 20px; height: 20px;
    background: var(--name-grey);
  }
  .brand__name {
    font-family: "Roboto", Arial, sans-serif;
    font-weight: 400;
    font-size: 26px;
    color: var(--name-grey);
  }
  .about__heading {
    font-weight: 700;
    font-size: 16px;
    color: var(--brand-blue);
    letter-spacing: 0.5px;
    margin-bottom: 4px;
  }
  .about__text {
    font-size: 17px;
    line-height: 1.3;
    margin-bottom: 16px;
  }
  /* Front side */
  .card--contact {
    top: 474px;
    background: var(--card-dark);
    color: var(--text-white);
  }
  .card__photo {
    position: absolute; inset: 0;
    background:
      radial-gradient(ellipse at 65% 35%, rgba(90,100,100,0.35), transparent 60%),
      linear-gradient(180deg, #1f2428 0%, #2a302e 55%, #1a1d1f 100%);
  }
  .contact {
    position: absolute;
    top: 70px; left: 0; right: 0;
    display: flex;
    justify-content: center;
    align-items: flex-start;
  }
  .person { text-align: right; padding-right: 22px; }
  .person__name {
    font-family: "Roboto Condensed", Arial, sans-serif;
    font-weight: 700;
    font-size: 34px;
    color: var(--brand-blue);
    line-height: 1;
  }
  .person__title {
    font-size: 17px;
    font-weight: 500;
    letter-spacing: 0.5px;
    margin-top: 4px;
  }
  .contact__rule {
    width: 1px; height: 76px;
    background: var(--rule);
  }
  .details { list-style: none; padding-left: 22px; padding-top: 4px; }
  .details li {
    display: flex; align-items: center; gap: 10px;
    font-size: 16px; font-weight: 500;
    line-height: 1.25;
  }
  .details svg { width: 14px; height: 14px; flex: none; fill: var(--icon-blue); }
  .pitch {
    position: absolute;
    left: 24px; right: 24px; top: 218px;
    text-align: center;
    font-family: "Roboto Condensed", Arial, sans-serif;
    font-size: 19px;
    line-height: 1.3;
  }
  .pitch__dot { color: var(--brand-navy); }
</style>
</head>
<body>

<section class="card card--about">
  <div class="brand">
    <span class="brand__mark"></span>
    <span class="brand__name">KRV Home Solutions LLC</span>
  </div>
  <h2 class="about__heading">WHO WE ARE</h2>
  <p class="about__text">We are a Faith based Real Estate Investment Company. We pay cash for homes in any condition and can close quick. Whatever the reason you need to sell fast, we can help. We believe in creating win-win solutions to help</p>
  <h2 class="about__heading">WHAT WE DO</h2>
  <p class="about__text">Buy houses, land, or commercial property as is.<br>We find solutions to make the process of selling simple and fair.</p>
</section>

<section class="card card--contact">
  <div class="card__photo" role="img" aria-label="Darkened photograph of a suburban house at dusk"></div>
  <div class="contact">
    <div class="person">
      <div class="person__name">JORDAN VALE</div>
      <div class="person__title">PRINCIPAL-ACQUISITIONS</div>
    </div>
    <div class="contact__rule"></div>
    <ul class="details">
      <li><svg viewBox="0 0 24 24"><path d="M6.6 10.8a15 15 0 0 0 6.6 6.6l2.2-2.2a1 1 0 0 1 1-.25 11.4 11.4 0 0 0 3.6.6 1 1 0 0 1 1 1V20a1 1 0 0 1-1 1A17 17 0 0 1 3 4a1 1 0 0 1 1-1h3.5a1 1 0 0 1 1 1c0 1.25.2 2.45.6 3.6a1 1 0 0 1-.25 1z"/></svg>555-214-0937</li>
      <li><svg viewBox="0 0 24 24"><path d="M2 5h20v14H2z"/><path d="M3 6l9 7 9-7" fill="none" stroke="#1c2024" stroke-width="2"/></svg>KRVHOMESOLUTIONS@fernmail.example</li>
      <li><svg viewBox="0 0 24 24"><circle cx="12" cy="12" r="10"/></svg>KRVHOMESOLUTIONS.example</li>
    </ul>
  </div>
  <p class="pitch">Pay all cash. Buy in as is condition. <span class="pitch__dot">•</span> No fees,Commisions or closing costs.<br>Close quick. No hassles with solutions to meet your unique situation.<br>Call today for an offer within 24 hours.</p>
</section>

</body>
</html>
```